Business card for law firm

Need business card for new law firm. Think confident, authoritative, conservative, but not stuffy or old-fashioned.

Contact Information for Business Card

Content for card - logo (uploaded), plus the following:

Paul Whitcombe (larger font)
Managing Partner (larger font, but not as large as name)
Level 9, 7 Ferris Lane
Sydney NSW 2000
Main Tel 02 9364 2710
Direct Tel 02 8472 3159
Email paul@qvlegal.com.au
www.qvlegal.com.au

Letterhead design should include logo plus:
Level 9, 7 Ferris Lane
Sydney NSW 2000
Tel 02 8472 3159
www.qvlegal.com.au

```html
<!DOCTYPE html>
<html lang="en">
<head>
<meta charset="utf-8">
<title>Quayvale Legal — Letterhead</title>
<link rel="stylesheet" href="https://fonts.googleapis.com/css2?family=Open+Sans:wght@400;600&family=Lato:wght@400;700&display=swap">
<style>
  :root {
    --navy: #0d1f5c;
    --ink: #4d4d4d;
    --ink-strong: #333333;
    --paper: #ffffff;
  }
  html, body {
    margin: 0;
    padding: 0;
    width: 1040px;
    height: 1200px;
    overflow: hidden;
    background: var(--paper);
  }
  .letterhead {
    position: relative;
    width: 1040px;
    height: 1200px;
    background: var(--paper);
    font-family: "Open Sans", Arial, sans-serif;
    color: var(--ink);
  }
  .brand {
    position: absolute;
    top: 40px;
    left: 0;
    width: 100%;
    text-align: center;
  }
  .brand-square {
    display: block;
    width: 64px;
    height: 64px;
    margin: 0 auto 34px;
    background: var(--navy);
  }
  .brand-name {
    font-family: "Open Sans", Arial, sans-serif;
    font-weight: 600;
    font-size: 34px;
    letter-spacing: 4px;
    color: var(--navy);
    line-height: 1;
    margin: 0;
  }
  .block {
    position: absolute;
    left: 98px;
    margin: 0;
    font-size: 16px;
    line-height: 18px;
  }
  .issue-date { top: 218px; }
  .recipient { top: 255px; }
  .salutation { top: 358px; }
  .body-copy {
    position: absolute;
    left: 98px;
    width: 840px;
    margin: 0;
    font-size: 16px;
    line-height: 27.2px;
    text-align: justify;
  }
  .para-1 { top: 406px; }
  .para-2 { top: 569px; }
  .para-3 { top: 677px; }
  .closing { top: 815px; }
  .signatory {
    position: absolute;
    left: 98px;
    top: 888px;
    margin: 0;
  }
  .signatory-name {
    display: block;
    font-size: 20px;
    font-weight: 600;
    color: var(--ink-strong);
    line-height: 26px;
  }
  .signatory-title {
    display: block;
    font-size: 16px;
    line-height: 26px;
  }
  .footer-band {
    position: absolute;
    left: 0;
    top: 1135px;
    width: 100%;
    height: 65px;
    background: var(--navy);
    color: #ffffff;
    font-family: "Lato", Arial, sans-serif;
    font-size: 19px;
  }
  .footer-item {
    position: absolute;
    top: 0;
    line-height: 65px;
    white-space: nowrap;
  }
  .footer-item strong { font-weight: 700; }
  .footer-phone { left: 112px; }
  .footer-web { left: 315px; }
  .footer-address { left: 567px; }
</style>
</head>
<body>
<main class="letterhead">
  <header class="brand">
    <span class="brand-square" aria-hidden="true"></span>
    <p class="brand-name">QUAYVALE LEGAL</p>
  </header>

  <p class="block issue-date">Issuing Date: May 5, 2018</p>
  <p class="block recipient">Name Of Employee Mr. XYZABC<br>Address of Employee<br>Address Line 2 etc..</p>
  <p class="block salutation">Dear Mr.XYZABC</p>

  <p class="body-copy para-1">Lorem Ipsum has been the industry's standard dummy text ever since the 1500s, when an unknown printer took a galley of type and scrambled it to make a type specimen book. It has survived not only five centuries, but also the leap into electronic typesetting, remaining essentially unchanged. It was popularised in the 1960s with the release of Lettercraft sheets containing Lorem Ipsum passages, and more recently with desktop publishing software like Pagewright Studio including versions of Lorem Ipsum.</p>

  <p class="body-copy para-2">Lorem Ipsum is simply dummy text of the printing and typesetting industry. Lorem Ipsum has been the industry's standard dummy text ever since the 1500s, when an unknown printer took a galley of type and scrambled it to make a type specimen book.</p>

  <p class="body-copy para-3">It has survived not only five centuries, but also the leap into electronic typesetting, remaining essentially unchanged. It was popularised in the 1960s with the release of Lettercraft sheets containing Lorem IpsumIpsum passages.</p>

  <p class="block closing">Yours Sincerely</p>

  <p class="signatory">
    <span class="signatory-name">Daniel Harper</span>
    <span class="signatory-title">Managing Director</span>
  </p>

  <footer class="footer-band">
    <span class="footer-item footer-phone"><strong>P:</strong> 02 8472 3159</span>
    <span class="footer-item footer-web"><strong>W:</strong> www.qvlegal.com.au</span>
    <span class="footer-item footer-address">Level 9, 7 Ferris Lane Sydney NSW 2000</span>
  </footer>
</main>
</body>
</html>
```